Velmora Solutions GAP Brochure Design Project

We are looking for a designer to create a point of sale brochure, the item will be used by Motor Dealers when they are selling our product to their customers, the product is an insurance product that covers the difference between the purchase price of the vehicle and the amount offered by the insurance company in the event the car is stolen or written off by the insurance company. Therefore we are look at a Business to Retail Customer relationship.
Please note we are in the process of designing a logo via Brindlework that will need to be used in the brochure. I have attached an example of a competitors POS. I am not concerned about including all of the terms and conditions and would prefer to keep the design as a two sided folded but obviously we will need some space for text. This is used by sales people as a sales aid.
Reason: The reference document did not upload, please let me know if you need further information.
Industry/Entity Type
Insurance
Look and feel
Each slider illustrates characteristics of the customer's brand and the style your logo design should communicate.

```html
<!DOCTYPE html>
<html lang="en">
<head>
<meta charset="utf-8">
<title>Velmora Solutions – Brochure Inside Spread</title>
<link rel="stylesheet" href="https://fonts.googleapis.com/css2?family=Open+Sans:wght@300;400;600;700&family=Roboto+Condensed:wght@400;700&display=swap">
<style>
  :root{
    --brand-red:#e21f26;
    --deep-red:#8e1118;
    --mid-red:#c4161f;
    --ink-grey:#58595b;
    --soft-grey:#6d6e71;
    --bar-grey:#8a8b8d;
    --paper:#ffffff;
    --backdrop:#ebebec;
    --text-dark:#3d3d3f;
  }
  *{box-sizing:border-box;margin:0;padding:0}
  html,body{width:1200px;height:767px;overflow:hidden;background:var(--backdrop)}
  body{font-family:"Open Sans",Arial,sans-serif;position:relative}
  .spread{position:absolute;left:106px;top:13px;width:988px;height:740px;background:var(--paper);overflow:hidden}

  .brand{position:absolute;left:26px;top:34px;display:flex;align-items:center;gap:10px;font-weight:700;font-size:34px;color:var(--ink-grey);letter-spacing:-1px}
  .brand__dot{width:38px;height:38px;border-radius:50%;background:var(--brand-red)}

  .headline{position:absolute;left:20px;top:126px;font-family:"Roboto Condensed",Arial Narrow,sans-serif;font-weight:700;font-size:44px;color:var(--brand-red);letter-spacing:-1.5px}

  .services{position:absolute;top:228px;list-style:none;font-size:12.5px;color:var(--text-dark);line-height:16px}
  .services li::before{content:"•";color:var(--brand-red);margin-right:14px;font-size:14px}
  .services--a{left:52px}
  .services--b{left:274px}

  .tagline{position:absolute;left:494px;top:140px;color:var(--soft-grey);text-align:right}
  .tagline__lead{display:block;font-weight:300;font-size:34px;letter-spacing:-1px;line-height:38px;padding-right:28px}
  .tagline__lead span{color:var(--brand-red);font-weight:600}
  .tagline__main{display:block;font-family:"Roboto Condensed",Arial Narrow,sans-serif;font-weight:700;font-size:52px;letter-spacing:-2px;line-height:50px}
  .tagline__main em{font-style:normal;color:var(--brand-red)}

  .hero-photo{position:absolute;left:738px;top:18px;width:236px;height:272px}

  .section-label{position:absolute;left:18px;top:304px;font-weight:400;font-size:25px;color:var(--soft-grey)}
  .section-title{position:absolute;left:274px;top:296px;font-family:"Roboto Condensed",Arial Narrow,sans-serif;font-weight:700;font-size:37px;color:var(--ink-grey)}
  .rule{position:absolute;left:0;top:338px;width:100%;height:17px;background:var(--bar-grey)}

  .red-panel{position:absolute;left:0;top:355px;width:100%;height:385px;background:linear-gradient(100deg,var(--brand-red) 0%,var(--mid-red) 30%,var(--deep-red) 62%,var(--mid-red) 100%);color:#fff}
  .red-panel__wave{position:absolute;inset:0}

  .points{position:absolute;left:15px;top:6px;width:208px;list-style:none;font-family:Arial,Helvetica,sans-serif;font-size:11.6px;line-height:13.3px}
  .points li::before{content:"•";margin:0 6px 0 2px}
  .panel-brand{position:absolute;left:20px;top:306px;display:flex;align-items:center;gap:6px;font-weight:700;font-size:18px;letter-spacing:-.5px}
  .panel-brand__dot{width:20px;height:20px;border-radius:50%;background:#fff}

  .column{position:absolute;left:245px;top:8px;width:222px;font-size:12.4px;line-height:18px;text-align:justify}
  .column h3{font-weight:400;font-size:15.5px;line-height:20px;text-align-last:justify}
  .column p{margin-bottom:7px}

  .steps{position:absolute;left:516px;top:0;width:456px}
  .step{position:absolute;left:0;width:456px;font-size:12.4px;line-height:17px}
  .step h3{font-weight:400;font-size:20px;line-height:24px;display:flex;align-items:baseline;gap:12px}
  .step__num{font-weight:700;font-size:38px;color:var(--bar-grey);line-height:24px}
  .step__lead{font-size:15px}
  .step--1{top:10px}.step--2{top:120px}.step--3{top:230px}
  .step--3 p{text-align:justify;line-height:18px;margin-top:10px}
</style>
</head>
<body>
<main class="spread">
  <div class="brand"><span class="brand__dot"></span>Velmora Solutions</div>

  <h1 class="headline">Duis Aute Irure Dolor...</h1>

  <ul class="services services--a">
    <li>Asset Accumulation</li><li>Estate Planning</li><li>Asset Allocation</li>
  </ul>
  <ul class="services services--b">
    <li>Education Planning</li><li>Income Taxes</li><li>Disability</li>
  </ul>

  <div class="tagline">
    <span class="tagline__lead"><span>...</span>your choice</span>
    <span class="tagline__main">for succe<em>ss</em></span>
  </div>

  <svg class="hero-photo" role="img" aria-label="Photograph of a red car with a silver alloy wheel" viewBox="0 0 236 272">
    <defs>
      <linearGradient id="heroTone" x1="0" y1="0" x2="1" y2="1">
        <stop offset="0" stop-color="#d0212a"/>
        <stop offset=".55" stop-color="#7c0f14"/>
        <stop offset="1" stop-color="#2b2b2d"/>
      </linearGradient>
    </defs>
    <rect width="236" height="272" rx="24" fill="url(#heroTone)"/>
  </svg>

  <h2 class="section-label">Officia Deserunt</h2>
  <h2 class="section-title">RET IUSTO ODIO NISSIM QUI BLANDIT</h2>
  <div class="rule"></div>

  <section class="red-panel">
    <svg class="red-panel__wave" viewBox="0 0 988 385" preserveAspectRatio="none" aria-hidden="true">
      <path d="M230 385 C420 250 560 330 760 200 C860 140 940 160 988 120 L988 385Z" fill="#ffffff" opacity=".06"/>
      <path d="M480 0 C600 120 760 60 988 150 L988 0Z" fill="#000000" opacity=".08"/>
    </svg>

    <ul class="points">
      <li>Ut wisi enim aminim veniam quis nostrudexerci tation ullam</li>
      <li>Ret iusto odio nissim qui blandit praesent luptatum zril delenit augue duis dolore.</li>
      <li>Lorem ipsum dolor sit amet, consectuer adipiscing elit, sed diam nmy nibismod.</li>
      <li>Tincidunt ut laoreet dolore magna quam erat volutpat.</li>
      <li>Ut wisi enim ad minim veniam quis exerci tation corper suscipit lobortis.</li>
      <li>Ut wisi enim aminim veniam quis nostrudexerci tation ullam</li>
      <li>Tincidunt ut laoreet dolore magna quam erat volutpat.</li>
      <li>Ut wisi enim ad minim veniam quis exerci tation corper suscipit lobortis.</li>
      <li>Ut wisi enim aminim veniam quis nostrudexerci tation ullam</li>
    </ul>
    <div class="panel-brand"><span class="panel-brand__dot"></span>Velmora Solutions</div>

    <div class="column">
      <h3>Lorem ipsum dolor sit amet</h3>
      <p>Consectetur adipisicing elit, sed do eiusmod tempor incididunt ut labore et dolore magna aliqua. Ut enim ad minim veniam, quis nostrud exercitation ullamco laboris nisi ut aliquip ex ea commodo consequat. Duis aute irure dolor in reprehenderit in voluptate velit esse cillum dolore eu fugiat nulla pariatur. Excepteur sint occaecat cupidatat non proident.</p>
      <h3>Lorem ipsum dolor sit amet</h3>
      <p>Consectetur adipisicing elit, sed do eiusmod tempor incididunt ut labore et dolore magna aliqua. Ut enim ad minim veniam, quis nostrud exercitation ullamco laboris nisi ut aliquip ex ea commodo consequat. Duis aute irure dolor in reprehenderit in</p>
    </div>

    <div class="steps">
      <article class="step step--1">
        <h3><span class="step__num">1</span>Duis aute irure dolor</h3>
        <p><span class="step__lead">Lorem ipsum dolor sit amet</span> Consectetur adipisicing elit, sed do eiusmod tempor incididunt ut labore et dolore magna aliqua. Ut enim ad minim veniam, quis nostrud exercitation ullamco laboris nisi ut aliquip ex ea commodo</p>
      </article>
      <article class="step step--2">
        <h3><span class="step__num">2</span>Ut wisi enim aminim</h3>
        <p><span class="step__lead">Lorem ipsum dolor sit amet</span> Consectetur adipisicing elit, sed do eiusmod tempor incididunt ut labore et dolore magna aliqua. Ut enim ad minim veniam, quis nostrud exercitation ullamco laboris nisi ut aliquip ex ea commodo</p>
      </article>
      <article class="step step--3">
        <h3><span class="step__num">3</span>Excepteur sint occaecat</h3>
        <p><span class="step__lead">Lorem ipsum dolor sit amet</span> Consectetur adipisicing elit, sed do eiusmod tempor incididunt ut labore et dolore magna aliqua. Ut enim ad minim veniam, quis nostrud exercitation ullamco laboris nisi ut aliquip ex ea commodo consequat. Duis aute irure dolor in reprehenderit in voluptate velit esse cillum dolore eu fugiat nulla pariatur. Excepteur sint occaecat cupidatat non proident,</p>
      </article>
    </div>
  </section>
</main>
</body>
</html>
```